KORV PTY LTD - Business Cards

Design a modern business card - using the attached Designs.
Same design as on the front, apart from the names/numbers/emails to be different.
We want the cards to be very glossy to stand out, do I think the simple black/white/metallic will be effective.
Both lots of details below:

Tom Wrenshaw
Director
tom_korv@nulvane.com
0438 274 093

Lewis Corbyn
Director
lewis_korv@nulvane.com
0419 385 642

Industry/Entity Type

Business

```html
<!DOCTYPE html>
<html lang="en">
<head>
<meta charset="utf-8">
<title>KORV PTY LTD – Business Cards</title>
<link href="https://fonts.googleapis.com/css2?family=Open+Sans:wght@400;700&display=swap" rel="stylesheet">
<style>
  :root {
    --bg: #e9e7e4;
    --card-white: #fbfbfb;
    --card-silver: #e3e4e6;
    --card-black: #111214;
    --card-graphite: #3a3c40;
    --ink-dark: #3b3d41;
    --ink-light: #ffffff;
    --rule: #8a8c90;
  }
  * { box-sizing: border-box; margin: 0; padding: 0; }
  html, body {
    width: 1200px; height: 913px; overflow: hidden;
    background: var(--bg);
    font-family: "Open Sans", Arial, sans-serif;
  }
  .canvas { position: relative; width: 1200px; height: 913px; }
  .card {
    position: absolute; left: 320px;
    width: 560px; height: 320px;
    border-radius: 4px; overflow: hidden;
    box-shadow: 0 6px 18px rgba(0,0,0,.18);
  }
  .card--front { top: 100px; background: var(--card-white); }
  .card--back { top: 493px; background: var(--card-black); }

  .front-texture {
    position: absolute; inset: 0;
    background: linear-gradient(135deg, var(--card-white) 0%, var(--card-silver) 50%, var(--card-white) 100%);
  }
  .brand {
    position: absolute; display: flex; align-items: center; gap: 12px;
    color: var(--ink-dark); font-weight: 700; letter-spacing: .04em;
  }
  .brand__dot {
    border-radius: 50%; background: var(--ink-dark); flex: none;
  }
  .card--front .brand { left: 50%; top: 50%; transform: translate(-50%, -50%); font-size: 40px; }
  .card--front .brand__dot { width: 30px; height: 30px; }

  .back-art { position: absolute; inset: 0; }
  .card--back .brand { left: 400px; top: 50%; transform: translate(-50%, -50%); font-size: 22px; gap: 8px; }
  .card--back .brand__dot { width: 16px; height: 16px; }

  .contacts {
    position: absolute; left: 30px; top: 40px; width: 300px;
    color: var(--ink-light); text-align: center;
  }
  .contact__name { font-size: 22px; font-weight: 700; line-height: 1.2; }
  .contact__role { font-size: 12px; line-height: 1.4; opacity: .85; }
  .contact__line { font-size: 16px; line-height: 1.35; }
  .contacts__rule {
    height: 1px; width: 240px; margin: 14px auto; background: var(--rule);
  }
</style>
</head>
<body>
<main class="canvas">
  <section class="card card--front" aria-label="Business card front">
    <div class="front-texture" role="img" aria-label="Subtle silver diamond pattern background"></div>
    <div class="brand"><span class="brand__dot"></span>KORV PTY LTD</div>
  </section>

  <section class="card card--back" aria-label="Business card back">
    <svg class="back-art" width="560" height="320" viewBox="0 0 560 320" aria-hidden="true">
      <defs>
        <linearGradient id="gloss" x1="0" y1="0" x2="1" y2="1">
          <stop offset="0" stop-color="#4a4c50"/>
          <stop offset=".45" stop-color="#1a1b1e"/>
          <stop offset="1" stop-color="#0c0d0f"/>
        </linearGradient>
        <linearGradient id="paper" x1="0" y1="0" x2="1" y2="0">
          <stop offset="0" stop-color="#d9dadc"/>
          <stop offset=".3" stop-color="#f7f7f7"/>
          <stop offset="1" stop-color="#ffffff"/>
        </linearGradient>
      </defs>
      <rect width="560" height="320" fill="url(#gloss)"/>
      <path d="M300 0 Q232 170 330 320 L560 320 L560 0 Z" fill="url(#paper)"/>
    </svg>
    <div class="brand"><span class="brand__dot"></span>KORV PTY LTD</div>
    <div class="contacts">
      <div class="contact">
        <p class="contact__name">Tom Wrenshaw</p>
        <p class="contact__role">Director</p>
        <p class="contact__line">0438 274 093</p>
        <p class="contact__line">tom_korv@nulvane.com</p>
      </div>
      <div class="contacts__rule"></div>
      <div class="contact">
        <p class="contact__name">Lewis Corbyn</p>
        <p class="contact__role">Director</p>
        <p class="contact__line">0419 385 642</p>
        <p class="contact__line">lewis_korv@nulvane.com</p>
      </div>
    </div>
  </section>
</main>
</body>
</html>
```